Kestrada LLC, needs a web page no more than 5 pages (for now)

Kestrada is a general contractor. Our services include general contracting, design-build construction, disaster recovery and environmental remediation. Our main clients are PMX, TQ, State and Local Gov't Agencies, Hospitals and Schools. Kestrada is also a SDVOSB.

```html
<!DOCTYPE html>
<html lang="en">
<head>
<meta charset="utf-8">
<title>Kestrada LLC — General Contractor</title>
<link href="https://fonts.googleapis.com/css2?family=Montserrat:wght@400;500;600;700&family=Poppins:wght@400;500;600&display=swap" rel="stylesheet">
<style>
:root{
  --gold:#c8872f;
  --gold-light:#e3ad5f;
  --gold-dark:#9c6420;
  --ink:#0e0e0f;
  --ink-2:#1a1917;
  --white:#ffffff;
  --text:#333333;
  --muted:#6b6b6b;
  --cream:#f3e7d6;
}
*{margin:0;padding:0;box-sizing:border-box}
html,body{width:1200px;height:4862px;overflow:hidden}
body{position:relative;background:var(--white);font-family:'Poppins',sans-serif;color:var(--text)}
.abs{position:absolute}
.h-font{font-family:'Montserrat',sans-serif}
.gold{color:var(--gold)}
.btn{position:absolute;display:flex;align-items:center;justify-content:center;font-family:'Montserrat',sans-serif;font-weight:700;font-size:13px;color:var(--white);border-radius:5px;text-transform:uppercase;letter-spacing:.3px}
.btn-gold{background:linear-gradient(180deg,var(--gold-light),var(--gold-dark))}
.btn-dark{background:var(--ink)}
.photo{position:absolute}
.wordmark{position:absolute;font-family:'Montserrat',sans-serif;font-weight:500;color:var(--white);letter-spacing:2px;display:flex;align-items:center;gap:12px}
.wordmark .dot{width:14px;height:14px;border-radius:50%;background:var(--gold)}

/* header */
.site-header{position:absolute;left:0;top:0;width:1200px;height:120px;background:var(--ink)}
.topbar{position:absolute;left:425px;top:0;width:775px;height:38px;background:linear-gradient(90deg,var(--gold-dark),var(--gold-light));clip-path:polygon(22px 0,100% 0,100% 100%,0 100%);display:flex;align-items:center;gap:40px;padding-left:50px;font-size:12px;color:var(--white)}
.topbar span{display:flex;align-items:center;gap:8px}
.topbar svg{width:22px;height:22px}
.nav{position:absolute;left:340px;top:72px;display:flex;gap:0;font-family:'Montserrat',sans-serif;font-size:12.5px;font-weight:500;color:var(--white)}
.nav a{padding:0 18px;border-right:1px solid var(--white);line-height:14px;text-decoration:none;color:inherit}
.nav a:last-child{border-right:none}
.nav a.active{color:var(--gold);font-weight:700;padding-left:2px}

/* hero */
.hero{position:absolute;left:0;top:120px;width:1200px;height:654px;overflow:hidden;background:linear-gradient(110deg,#b27628 0%,#d49b4d 45%,#c48636 100%)}
.hero h1{position:absolute;left:120px;top:108px;font-family:'Montserrat',sans-serif;font-weight:500;font-size:38px;line-height:50px;color:var(--white);letter-spacing:.5px}
.hero p{position:absolute;left:124px;top:218px;font-size:20px;line-height:32px;color:var(--white)}

/* services */
.services{position:absolute;left:0;top:774px;width:1200px;height:510px;background:linear-gradient(180deg,#111 0%,#17150f 100%)}
.sec-title{font-family:'Montserrat',sans-serif;font-weight:500;font-size:38px;color:var(--white);letter-spacing:.5px}
.rule{position:absolute;height:3px;width:64px;background:var(--gold)}
.services p{position:absolute;left:120px;top:172px;width:265px;font-size:13.5px;line-height:24.5px;color:var(--white);text-align:justify}
.svc-card{position:absolute;top:62px;width:288px;height:352px}
.svc-card .photo{left:0;top:0;width:288px;height:255px}
.svc-card .body{position:absolute;left:22px;top:200px;width:244px;height:152px;background:var(--white);border-radius:3px;text-align:center}
.svc-card h3{margin-top:34px;font-family:'Montserrat',sans-serif;font-weight:500;font-size:18px;line-height:26px;color:#111}
.svc-card .btn{left:52px;top:100px;width:138px;height:42px}

/* about */
.about{position:absolute;left:0;top:1284px;width:1200px;height:566px;background:var(--white)}
.about p{position:absolute;left:628px;top:169px;width:395px;font-size:13px;line-height:24.5px;color:#444;text-align:justify}

/* stats */
.stats{position:absolute;left:0;top:1850px;width:1200px;height:282px;background:var(--ink-2)}
.stats .panel{position:absolute;left:476px;top:0;width:724px;height:282px;background:linear-gradient(90deg,#b97a2b,#cf9446 60%,#b8792c)}
.stats h2{position:absolute;left:120px;top:66px;font-family:'Montserrat',sans-serif;font-weight:500;font-size:28px;line-height:37.5px;color:var(--white)}
.stat{position:absolute;top:66px;width:220px;color:var(--white)}
.stat svg{width:64px;height:64px}
.stat b{display:block;margin-top:14px;font-family:'Montserrat',sans-serif;font-weight:600;font-size:36px}
.stat span{display:block;margin-top:6px;font-size:15px;line-height:24px}

/* serve */
.serve{position:absolute;left:0;top:2132px;width:1200px;height:723px;background:linear-gradient(180deg,#121212,#1a1814)}
.serve-item{position:absolute;width:215px;color:var(--white)}
.serve-item svg{width:52px;height:52px}
.serve-item h3{margin-top:18px;font-family:'Montserrat',sans-serif;font-weight:600;font-size:17px;line-height:24px}
.serve-item p{margin-top:8px;font-size:13px;line-height:24px}

/* projects */
.projects{position:absolute;left:0;top:2855px;width:1200px;height:891px;background:var(--white)}
.projects .photo{width:307px;height:246px}

/* testimonials */
.reviews{position:absolute;left:0;top:3746px;width:1200px;height:594px;background:linear-gradient(180deg,#f6ede1,#efe0cb)}
.review{position:absolute;top:188px;width:453px;height:317px;background:var(--white);border-radius:3px;box-shadow:0 4px 18px rgba(0,0,0,.06);padding:28px 26px}
.review .stars{color:var(--gold);font-size:18px;letter-spacing:2px}
.review p{margin-top:14px;font-size:13.5px;line-height:26px;color:#444}
.review .avatar{position:absolute;left:22px;top:220px;width:86px;height:86px;border-radius:50%;background:linear-gradient(160deg,#c9d3da,#8a98a3)}
.review .name{position:absolute;left:130px;top:236px;font-family:'Montserrat',sans-serif;font-weight:600;font-size:16px;color:var(--gold)}
.review .role{position:absolute;left:130px;top:264px;font-size:13px;color:#555}
.arrow-btn{position:absolute;top:330px;width:34px;height:34px;border:2px solid var(--gold);border-radius:50%;display:flex;align-items:center;justify-content:center}

/* footer */
.site-footer{position:absolute;left:0;top:4340px;width:1200px;height:522px}
.foot-col{position:absolute;color:var(--white);font-size:14.5px}
.foot-col h4{font-family:'Montserrat',sans-serif;font-weight:600;font-size:16.5px;letter-spacing:.4px;margin-bottom:18px}
.foot-col li{list-style:none;display:flex;align-items:center;gap:10px;height:33px}
.contact-row{display:flex;gap:14px;align-items:flex-start;margin-bottom:18px;line-height:26px}
.contact-row i{flex:none;width:32px;height:32px;border:1.5px solid var(--gold);border-radius:50%;display:flex;align-items:center;justify-content:center}
.copyright{position:absolute;left:0;top:475px;width:1200px;text-align:center;font-size:12.5px;color:var(--white)}
</style>
</head>
<body>

<!-- HEADER -->
<header class="site-header">
  <div class="wordmark" style="left:119px;top:44px;font-size:28px"><span class="dot"></span>KESTRADA</div>
  <div class="topbar">
    <span><svg viewBox="0 0 24 24"><circle cx="12" cy="12" r="11" fill="none" stroke="#fff" stroke-width="1.5"/><path d="M8.5 7h2l1 3-1.5 1a7 7 0 0 0 3 3l1-1.5 3 1v2c0 .6-.4 1-1 1A9 9 0 0 1 7.5 8c0-.6.4-1 1-1z" fill="#fff"/></svg>+1 555 014 2290</span>
    <span><svg viewBox="0 0 24 24"><circle cx="12" cy="12" r="11" fill="none" stroke="#fff" stroke-width="1.5"/><rect x="6.5" y="8" width="11" height="8" fill="none" stroke="#fff" stroke-width="1.4"/><path d="M6.5 8l5.5 4.5L17.5 8" fill="none" stroke="#fff" stroke-width="1.4"/></svg>info@kestrada.com</span>
    <span><svg viewBox="0 0 24 24"><circle cx="12" cy="12" r="11" fill="none" stroke="#fff" stroke-width="1.5"/><path d="M12 18s-4.5-4.5-4.5-7.5a4.5 4.5 0 0 1 9 0C16.5 13.5 12 18 12 18z" fill="#fff"/><circle cx="12" cy="10.5" r="1.6" fill="#b97a2b"/></svg>418 Harbor Parkway, Suite 2</span>
  </div>
  <nav class="nav">
    <a class="active" href="#">HOME</a><a href="#">ABOUT US</a><a href="#">OUR SERVICES</a><a href="#">WHO WE SERVE</a><a href="#">CONTACT US</a>
  </nav>
  <div class="btn btn-gold" style="left:949px;top:61px;width:131px;height:43px">GET A QUOTE</div>
</header>

<!-- HERO -->
<section class="hero">
  <div class="photo" role="img" aria-label="Two smiling construction workers in orange hard hats and safety vests, one holding a tablet" style="left:620px;top:10px;width:580px;height:600px;background:radial-gradient(ellipse at 55% 45%,#e8c38a 0%,#c58a3c 55%,rgba(197,138,60,0) 75%)"></div>
  <h1>BUILDING WITH INTEGRITY.<br>DELIVERING WITH PRECISION.</h1>
  <p>Trusted General Contractor for Federal, State, and<br>Institutional Projects</p>
  <div class="btn btn-dark" style="left:119px;top:295px;width:139px;height:42px">GET STARTED</div>
  <svg class="abs" style="left:0;top:0" width="1200" height="654" viewBox="0 0 1200 654">
    <defs><linearGradient id="heroGold" x1="0" x2="1"><stop offset="0" stop-color="#8a5a1c"/><stop offset=".5" stop-color="#e2ab5c"/><stop offset="1" stop-color="#8a5a1c"/></linearGradient></defs>
    <polygon points="0,440 600,600 1200,440 1200,654 0,654" fill="#0f0f10"/>
    <polygon points="0,462 600,615 1200,462 1200,490 600,648 0,490" fill="url(#heroGold)"/>
    <polygon points="0,490 600,648 1200,490 1200,654 0,654" fill="#111"/>
  </svg>
</section>

<!-- SERVICES -->
<section class="services">
  <h2 class="sec-title abs" style="left:118px;top:92px">OUR <span class="gold">SERVICES</span></h2>
  <div class="rule" style="left:120px;top:148px"></div>
  <p>Our team delivers full general contracting, design-build, disaster recovery and remediation work for public clients, with a focus on safe, on-time delivery.</p>
  <div class="btn btn-gold" style="left:119px;top:317px;width:140px;height:45px">GET A QUOTE</div>

  <div class="svc-card" style="left:445px">
    <div class="photo" role="img" aria-label="Smiling site worker in a hard hat in front of a building under construction" style="background:linear-gradient(160deg,#9fb6c8,#7b6a55 60%,#3e3428)"></div>
    <div class="body"><h3>Environmental<br>Remediation</h3><div class="btn btn-gold">READ MORE</div></div>
  </div>
  <div class="svc-card" style="left:757px">
    <div class="photo" role="img" aria-label="Hands reviewing architectural floor plans on a table" style="background:linear-gradient(160deg,#8a8f92,#c9c5bd 55%,#6a6660)"></div>
    <div class="body"><h3>Design-Build<br>Construction</h3><div class="btn btn-gold">READ MORE</div></div>
  </div>
  <div class="svc-card" style="left:1068px">
    <div class="photo" role="img" aria-label="Crew clearing debris with an excavator after a disaster" style="background:linear-gradient(160deg,#7fa3c2,#a88b5c 60%,#5a4630)"></div>
    <div class="body"><h3>Disaster<br>Recovery</h3><div class="btn btn-gold">READ MORE</div></div>
  </div>
</section>

<!-- ABOUT -->
<section class="about">
  <div class="photo" role="img" aria-label="Silhouette of an engineer holding a model city skyline with cranes, in warm gold tones" style="left:0;top:46px;width:576px;height:520px;background:radial-gradient(ellipse at 45% 55%,#c9914a 0%,#a66c28 40%,rgba(255,255,255,0) 72%)"></div>
  <h2 class="sec-title abs" style="left:628px;top:84px;color:#111">ABOUT <span class="gold">US</span></h2>
  <div class="rule" style="left:630px;top:138px"></div>
  <p>Kestrada is a general contracting firm serving public agencies, hospitals and schools. We plan, manage and build projects of every size with care for budget, schedule and safety. Our crews and partners bring years of field experience to each site, and our project leads keep owners informed from the first survey to the final walkthrough. We take pride in building facilities that serve communities well for decades to come.</p>
  <div class="btn btn-gold" style="left:630px;top:414px;width:140px;height:46px">READ MORE</div>
</section>

<!-- STATS -->
<section class="stats">
  <div class="panel"></div>
  <h2>PARTNERING WITH<br><span class="gold">PMX, TQ, HOSPITALS,<br>AND SCHOOLS<br>NATIONWIDE.</span></h2>
  <div class="stat" style="left:513px">
    <svg viewBox="0 0 64 64" fill="none" stroke="#fff" stroke-width="2"><rect x="8" y="10" width="40" height="46"/><path d="M16 22h24M16 32h16M16 42h12M40 38l14-22 4 3-14 22-6 3z"/></svg>
    <b>250+</b><span>Projects Completed</span>
  </div>
  <div class="stat" style="left:740px">
    <svg viewBox="0 0 64 64" fill="none" stroke="#fff" stroke-width="2"><path d="M8 56l14-14M18 50l10-10 8 4 10-14M44 30l8-16M48 10l6 4-2 6"/><circle cx="30" cy="22" r="6"/></svg>
    <b>20+</b><span>Years of Experience</span>
  </div>
  <div class="stat" style="left:968px">
    <svg viewBox="0 0 64 64" fill="none" stroke="#fff" stroke-width="2"><circle cx="32" cy="24" r="6"/><circle cx="16" cy="30" r="5"/><circle cx="48" cy="30" r="5"/><path d="M22 52c0-8 4-14 10-14s10 6 10 14M6 52c0-6 4-12 10-12M58 52c0-6-4-12-10-12"/></svg>
    <b>50+</b><span>Agencies &amp;<br>Institutions Served</span>
  </div>
</section>

<!-- WHO WE SERVE -->
<section class="serve">
  <div class="photo" role="img" aria-label="City skyline at sunset seen beside a glass office tower" style="left:119px;top:104px;width:451px;height:512px;background:linear-gradient(180deg,#7d8fa6 0%,#e3a55a 45%,#8a5a2a 75%,#2a241d 100%)"></div>
  <h2 class="sec-title abs" style="left:642px;top:116px">WHO WE <span class="gold">SERVE</span></h2>
  <div class="rule" style="left:644px;top:172px"></div>
  <div class="serve-item" style="left:642px;top:213px">
    <svg viewBox="0 0 52 52" fill="none" stroke="#c8872f" stroke-width="2"><rect x="8" y="20" width="36" height="26"/><path d="M4 20L26 6l22 14M18 46V32h16v14"/></svg>
    <h3>Department of Civic<br>Works (PMX)</h3><p>Secure, efficient, and compliant infrastructure projects.</p>
  </div>
  <div class="serve-item" style="left:874px;top:213px">
    <svg viewBox="0 0 52 52" fill="none" stroke="#c8872f" stroke-width="2"><rect x="10" y="12" width="32" height="34"/><path d="M26 18v12M20 24h12M22 46V38h8v8"/></svg>
    <h3>Department of Public<br>Health (TQ)</h3><p>Facilities built to support community healthcare and services.</p>
  </div>
  <div class="serve-item" style="left:642px;top:429px">
    <svg viewBox="0 0 52 52" fill="none" stroke="#c8872f" stroke-width="2"><path d="M4 18L26 6l22 12zM8 46h36M10 22v20M20 22v20M32 22v20M42 22v20"/></svg>
    <h3>State &amp; Local<br>Government<br>Agencies</h3><p>Reliable construction for community infrastructure.</p>
  </div>
  <div class="serve-item" style="left:874px;top:429px">
    <svg viewBox="0 0 52 52" fill="none" stroke="#c8872f" stroke-width="2"><rect x="6" y="20" width="18" height="26"/><rect x="24" y="8" width="22" height="38"/><path d="M35 14v8M31 18h8M10 28h10M10 36h10M30 30h10M30 38h10"/></svg>
    <h3>Hospitals and<br>Schools.</h3><p>Modern environments and functional spaces for learning and patient care</p>
  </div>
</section>

<!-- PROJECTS -->
<section class="projects">
  <h2 class="sec-title abs" style="left:0;width:1200px;top:90px;text-align:center;color:#111">OUR <span class="gold">PROJECTS</span></h2>
  <div class="rule" style="left:568px;top:156px"></div>
  <div class="photo" role="img" aria-label="Hospital tower with emergency entrance signage" style="left:119px;top:196px;background:linear-gradient(180deg,#7fa6d6,#c9d2da 55%,#6c7785)"></div>
  <div class="photo" role="img" aria-label="White public building with arched entrance and flagpole" style="left:447px;top:196px;background:linear-gradient(180deg,#3f7fd4,#a9c5e6 45%,#e6e2dc 70%,#7a7770)"></div>
  <div class="photo" role="img" aria-label="Modern curved hospital building under blue sky" style="left:774px;top:196px;background:linear-gradient(180deg,#4f86cf,#c7d7ea 50%,#eef0f0 80%,#8b8f93)"></div>
  <div class="photo" role="img" aria-label="School entrance with a yellow school bus and students" style="left:119px;top:460px;background:linear-gradient(180deg,#8eb2d8,#9c7b5e 45%,#8c8a84 75%,#d6a32e)"></div>
  <div class="photo" role="img" aria-label="Multi-storey school building in red brick and white panels" style="left:447px;top:460px;background:linear-gradient(180deg,#2f6fd0,#9cbfea 45%,#d8dbe0 70%,#a9463a)"></div>
  <div class="photo" role="img" aria-label="Aerial view of a large campus building among autumn trees" style="left:774px;top:460px;background:linear-gradient(180deg,#b9c8d6,#bfa383 40%,#8a7a5e 75%,#7d6a4c)"></div>
  <div class="btn btn-gold" style="left:528px;top:761px;width:138px;height:41px">VIEW MORE</div>
</section>

<!-- TESTIMONIALS -->
<section class="reviews">
  <h2 class="sec-title abs" style="left:0;width:1200px;top:80px;text-align:center;color:#111">WHAT OUR <span class="gold">CLIENTS SAY</span></h2>
  <div class="rule" style="left:568px;top:146px"></div>
  <div class="arrow-btn" style="left:34px"><svg width="14" height="14" viewBox="0 0 14 14"><path d="M9 2L4 7l5 5" fill="none" stroke="#c8872f" stroke-width="2"/></svg></div>
  <div class="arrow-btn" style="left:1119px"><svg width="14" height="14" viewBox="0 0 14 14"><path d="M5 2l5 5-5 5" fill="none" stroke="#c8872f" stroke-width="2"/></svg></div>
  <div class="review" style="left:138px">
    <div class="stars">★★★★★</div>
    <p>Kestrada managed our clinic expansion with clear updates every week. The crew kept the site safe and tidy, and the final handover came ahead of our planned opening date.</p>
    <div class="avatar" role="img" aria-label="Client portrait"></div>
    <div class="name">Marcus</div><div class="role">Client</div>
  </div>
  <div class="review" style="left:615px">
    <div class="stars">★★★★★</div>
    <p>From design to build, the team handled every detail of our school wing renovation. Costs stayed on budget and the staff were always quick to answer our questions.</p>
    <div class="avatar" role="img" aria-label="Client portrait"></div>
    <div class="name">Owen</div><div class="role">Client</div>
  </div>
</section>

<!-- FOOTER -->
<footer class="site-footer">
  <svg class="abs" style="left:0;top:0" width="1200" height="522" viewBox="0 0 1200 522">
    <defs><linearGradient id="footGold" x1="0" x2="1"><stop offset="0" stop-color="#7a4c16"/><stop offset=".5" stop-color="#d99e4d"/><stop offset="1" stop-color="#7a4c16"/></linearGradient></defs>
    <polygon points="0,175 600,0 1200,175 1200,522 0,522" fill="url(#footGold)"/>
    <polygon points="0,192 600,42 1200,192 1200,522 0,522" fill="#0f0f10"/>
  </svg>
  <div class="wordmark" style="left:151px;top:262px;font-size:28px"><span class="dot"></span>KESTRADA</div>
  <div class="foot-col" style="left:396px;top:210px">
    <h4>MAIN LINKS</h4>
    <ul>
      <li><svg width="14" height="12" viewBox="0 0 14 12"><path d="M0 6h11M7 1l5 5-5 5" fill="none" stroke="#fff" stroke-width="2"/></svg>Home</li>
      <li><svg width="14" height="12" viewBox="0 0 14 12"><path d="M0 6h11M7 1l5 5-5 5" fill="none" stroke="#fff" stroke-width="2"/></svg>About</li>
      <li><svg width="14" height="12" viewBox="0 0 14 12"><path d="M0 6h11M7 1l5 5-5 5" fill="none" stroke="#fff" stroke-width="2"/></svg>Services</li>
      <li><svg width="14" height="12" viewBox="0 0 14 12"><path d="M0 6h11M7 1l5 5-5 5" fill="none" stroke="#fff" stroke-width="2"/></svg>Who we serve</li>
      <li><svg width="14" height="12" viewBox="0 0 14 12"><path d="M0 6h11M7 1l5 5-5 5" fill="none" stroke="#fff" stroke-width="2"/></svg>Contact</li>
    </ul>
  </div>
  <div class="foot-col" style="left:592px;top:210px">
    <h4>CONTACT US</h4>
    <div class="contact-row"><i><svg width="14" height="16" viewBox="0 0 14 16"><path d="M7 15S1.5 9.5 1.5 6a5.5 5.5 0 0 1 11 0C12.5 9.5 7 15 7 15z" fill="none" stroke="#c8872f" stroke-width="1.6"/></svg></i><span>Kestrada<br>United States</span></div>
    <div class="contact-row"><i><svg width="14" height="14" viewBox="0 0 14 14"><path d="M2 1h3l1 3-1.5 1.2a8 8 0 0 0 4.3 4.3L10 8l3 1v3c0 .6-.4 1-1 1A11 11 0 0 1 1 2c0-.6.4-1 1-1z" fill="none" stroke="#c8872f" stroke-width="1.4"/></svg></i><span>+1 555 014 2290</span></div>
    <div class="contact-row"><i><svg width="15" height="12" viewBox="0 0 15 12"><rect x="1" y="1" width="13" height="10" fill="none" stroke="#c8872f" stroke-width="1.4"/><path d="M1 1l6.5 5.5L14 1" fill="none" stroke="#c8872f" stroke-width="1.4"/></svg></i><span>info@kestrada.com</span></div>
  </div>
  <div class="foot-col" style="left:855px;top:210px">
    <h4>KESTRADA IS A SDVOSB</h4>
  </div>
  <div class="abs" style="left:862px;top:248px;width:164px;height:164px;border-radius:50%;border:3px solid #fff"></div>
  <div class="abs" style="left:125px;top:442px;width:955px;height:1px;background:#fff"></div>
  <div class="copyright">© 2025 Kestrada | All Rights Reserved</div>
</footer>

</body>
</html>
```